UI/ UX Design for ERP Software

We need a new UX/UI interface for a ERP software for property managers. Our CMMS / ERP solution is made based on responsive design technologies and is coded in PHP.
The overall UX to be similar to Tev Ulna - easy navigation, intuitive menus.

Industry/Entity Type

Property Management

Number of Pages Required

5+ page

Requirements
Must have
• Round dock buttons
Consistent icons across the application
Enough Spacing between buttons/icons/ menu
Consistent Font
Nice to have
• We would like the UX to allow the users to use the application without /minimum training.
Should not have
• we don't want anything that is classic with respect to UX

```html
<!DOCTYPE html>
<html lang="en">
<head>
<meta charset="utf-8">
<title>Domora – Active Dashboard</title>
<link href="https://fonts.googleapis.com/css2?family=Poppins:wght@400;500;600;700&display=swap" rel="stylesheet">
<style>
:root{
  --blue:#0a8cf0;
  --blue-light:#1fb0ff;
  --ink:#3e4a5c;
  --ink-soft:#8a94a3;
  --page:#f3f4f7;
  --card:#ffffff;
  --pill:#eceef1;
  --grid:#eef0f3;
}
*{box-sizing:border-box;margin:0;padding:0}
html,body{width:1200px;height:800px;overflow:hidden}
body{font-family:'Poppins',sans-serif;background:var(--page);color:var(--ink);position:relative}

.sidebar{position:absolute;left:0;top:0;width:251px;height:800px;background:var(--card)}
.brand{position:absolute;left:48px;top:30px;display:flex;align-items:center;gap:8px}
.brand-mark{width:26px;height:26px;background:var(--blue);border-radius:4px}
.brand-name{font-size:26px;font-weight:600;color:var(--blue)}
.nav{position:absolute;left:0;top:110px;list-style:none;width:100%}
.nav-item{height:53.3px;display:flex;align-items:center;padding-left:23px;font-size:13px;font-weight:500;color:var(--ink)}
.nav-item svg{width:22px;height:22px;margin-right:8px;flex:none;fill:none;stroke:var(--ink);stroke-width:1.6;stroke-linejoin:round;stroke-linecap:round}
.nav-item.is-active{font-size:15.5px;font-weight:600}
.nav-item.is-active svg{stroke:var(--blue)}

.topbar{position:absolute;left:251px;top:0;width:949px;height:64px;background:linear-gradient(90deg,#0b7ff0,var(--blue-light))}
.search{position:absolute;left:26px;top:22px;display:flex;align-items:center;gap:10px;color:#dcefff;font-size:14px}
.search svg{width:18px;height:18px;fill:none;stroke:#fff;stroke-width:2}
.settings{position:absolute;left:715px;top:13px;width:38px;height:38px;border-radius:50%;background:rgba(255,255,255,.2);display:flex;align-items:center;justify-content:center}
.settings svg{width:20px;height:20px;fill:#fff}
.avatar{position:absolute;left:762px;top:13px;width:38px;height:38px;border-radius:50%;background:linear-gradient(135deg,#6a7b8c,#2e3945)}
.user{position:absolute;left:809px;top:17px;color:#fff;line-height:1}
.user-name{font-size:15px;font-weight:600}
.user-role{font-size:9.5px;font-weight:500;margin-top:3px}
.caret{position:absolute;left:910px;top:27px;width:11px;height:11px;fill:none;stroke:#fff;stroke-width:2}

.page-title{position:absolute;left:285px;top:126px;font-size:27px;font-weight:700;color:var(--ink)}

.stats{position:absolute;left:285px;top:176px;display:flex;gap:9px}
.stat{position:relative;width:169px;height:144px;background:var(--card);border-radius:6px}
.stat-icon{position:absolute;right:20px;top:14px;width:46px;height:46px;fill:none;stroke:var(--blue-light);stroke-width:1.6;stroke-linejoin:round}
.stat-label{position:absolute;left:15px;top:82px;font-size:12px;color:var(--ink-soft)}
.stat-value{position:absolute;left:15px;top:100px;font-size:16px;font-weight:600;color:var(--ink)}

.activity{position:absolute;left:285px;top:343px;width:878px;height:375px;background:var(--card);border-radius:6px}
.activity-chart{position:absolute;left:0;top:0;width:878px;height:375px}
.range{position:absolute;left:22px;top:33px;display:flex;align-items:center;gap:8px;font-size:12.5px;font-weight:500}
.range svg{width:16px;height:16px;fill:none;stroke:var(--ink);stroke-width:1.4}
.filter{position:absolute;top:30px;width:97px;height:25px;border-radius:13px;background:var(--pill);font-size:11.5px;font-weight:500;display:flex;align-items:center;justify-content:center;color:var(--ink)}
.legend{position:absolute;font-size:11.5px;font-weight:500;display:flex;align-items:center;gap:6px;color:var(--ink)}
.legend i{width:7px;height:7px;border-radius:50%;display:block}

.footer{position:absolute;left:251px;top:764px;width:949px;text-align:center;font-size:14.5px;font-weight:500;color:var(--ink)}
</style>
</head>
<body>

<aside class="sidebar">
  <div class="brand"><span class="brand-mark"></span><span class="brand-name">Domora</span></div>
  <ul class="nav">
    <li class="nav-item is-active"><svg viewBox="0 0 24 24"><path d="M3 16a9 9 0 1 1 18 0"/><path d="M12 16l4-5"/><circle cx="12" cy="16" r="1.5"/></svg>Dashboard</li>
    <li class="nav-item"><svg viewBox="0 0 24 24"><circle cx="9" cy="8" r="4"/><path d="M2 20c0-4 3-6 7-6s7 2 7 6"/><path d="M15 4a4 4 0 0 1 0 8M18 14c2 1 4 3 4 6"/></svg>Customers</li>
    <li class="nav-item"><svg viewBox="0 0 24 24"><path d="M3 11l9-8 9 8v10H3z"/></svg>Properties</li>
    <li class="nav-item"><svg viewBox="0 0 24 24"><path d="M3 11l9-8 9 8v10H3z"/></svg>Tenant</li>
    <li class="nav-item"><svg viewBox="0 0 24 24"><rect x="5" y="3" width="15" height="18" rx="1"/><circle cx="12.5" cy="10" r="2.5"/><path d="M8.5 17c0-2 2-3 4-3s4 1 4 3M3 7h3M3 12h3M3 17h3"/></svg>Contact</li>
    <li class="nav-item"><svg viewBox="0 0 24 24"><path d="M7 9a5 5 0 0 1 10 0z"/><circle cx="12" cy="12" r="3"/><path d="M5 21c0-4 3-6 7-6s7 2 7 6z"/></svg>Contractors</li>
    <li class="nav-item"><svg viewBox="0 0 24 24"><circle cx="9" cy="8" r="4"/><path d="M2 20c0-4 3-6 7-6s7 2 7 6"/><path d="M15 4a4 4 0 0 1 0 8M18 14c2 1 4 3 4 6"/></svg>Employees</li>
    <li class="nav-item"><svg viewBox="0 0 24 24"><rect x="6" y="3" width="15" height="18" rx="2"/><path d="M12 9h6M12 13h6M12 17h6"/><circle cx="6" cy="11" r="3"/></svg>Compliance Manag...</li>
    <li class="nav-item"><svg viewBox="0 0 24 24"><path d="M4 20L16 8M14 4l6 6M3 4l5 5M20 20l-9-9"/><circle cx="5" cy="19" r="2"/></svg>Prevent. Mainten...</li>
    <li class="nav-item"><svg viewBox="0 0 24 24"><rect x="4" y="3" width="16" height="18" rx="1"/><path d="M8 8h8M8 12h5M9 17l8-8"/></svg>Work Orders</li>
    <li class="nav-item"><svg viewBox="0 0 24 24"><path d="M2 5h3l3 11h11l2-8H7"/><circle cx="9" cy="20" r="1.5"/><circle cx="17" cy="20" r="1.5"/><circle cx="13" cy="6" r="3"/></svg>Purchase Orders</li>
    <li class="nav-item"><svg viewBox="0 0 24 24"><path d="M3 11l9-8 9 8v10H3z"/></svg>Property Inspections</li>
  </ul>
</aside>

<header class="topbar">
  <div class="search"><svg viewBox="0 0 24 24"><circle cx="10" cy="10" r="7"/><path d="M15 15l6 6"/></svg>Search...</div>
  <div class="settings"><svg viewBox="0 0 24 24"><path d="M12 2l2 3 3.5-.8.8 3.5 3 2-2 3 2 3-3 2-.8 3.5-3.5-.8-2 3-2-3-3.5.8-.8-3.5-3-2 2-3-2-3 3-2 .8-3.5L10 5z"/><circle cx="12" cy="12" r="3.5" fill="#3aa8f5"/></svg></div>
  <div class="avatar" role="img" aria-label="User profile photo"></div>
  <div class="user"><div class="user-name">Lena Harlow</div><div class="user-role">CEO founder</div></div>
  <svg class="caret" viewBox="0 0 12 12"><path d="M2 4l4 4 4-4"/></svg>
</header>

<h1 class="page-title">Active Dashboard</h1>

<section class="stats">
  <div class="stat">
    <svg class="stat-icon" viewBox="0 0 48 48"><rect x="4" y="20" width="20" height="24"/><rect x="24" y="6" width="18" height="38"/><path d="M24 6l9-4 9 4"/><path d="M8 25h4v4H8zM15 25h4v4h-4zM8 33h4v4H8zM15 33h4v4h-4zM28 12h4v4h-4zM35 12h4v4h-4zM28 20h4v4h-4zM35 20h4v4h-4zM28 28h4v4h-4zM35 28h4v4h-4zM28 36h4v4h-4zM35 36h4v4h-4z"/></svg>
    <div class="stat-label">Properties</div><div class="stat-value">3 homes</div>
  </div>
  <div class="stat">
    <svg class="stat-icon" viewBox="0 0 48 48"><rect x="4" y="4" width="24" height="40"/><path d="M8 10h16M8 16h4M14 16h4M20 16h4M8 22h4M14 22h4M8 28h4M8 34h4"/><circle cx="33" cy="24" r="5"/><path d="M22 44c0-8 5-11 11-11s11 3 11 11z"/></svg>
    <div class="stat-label">Tenants</div><div class="stat-value">8 Tenants</div>
  </div>
  <div class="stat">
    <svg class="stat-icon" viewBox="0 0 48 48"><rect x="6" y="12" width="28" height="32"/><path d="M6 4h28M9 1l-3 3 3 3M31 1l3 3-3 3M42 12v32M39 15l3-3 3 3M39 41l3 3 3-3"/></svg>
    <div class="stat-label">Properties Area</div><div class="stat-value">422,000.00 sq.ft</div>
  </div>
  <div class="stat">
    <svg class="stat-icon" viewBox="0 0 48 48"><path d="M4 20L24 4l20 16"/><path d="M8 18v26h32V18"/><rect x="12" y="22" width="24" height="10"/><circle cx="24" cy="13" r="3"/><path d="M4 44h40M16 36h16v8H16z"/></svg>
    <div class="stat-label">Rented Area</div><div class="stat-value">233,500.00 sq.ft</div>
  </div>
  <div class="stat">
    <svg class="stat-icon" viewBox="0 0 48 48"><circle cx="20" cy="20" r="15"/><path d="M31 31l13 13M12 16h4M12 24h4M19 16h10M19 20h10M19 24h10"/></svg>
    <div class="stat-label">Vacancies Area</div><div class="stat-value">188,500.00 sq.ft</div>
  </div>
</section>

<section class="activity">
  <svg class="activity-chart" viewBox="321 386 988 422" preserveAspectRatio="none" role="img" aria-label="Activity line chart across the month">
    <defs>
      <linearGradient id="areaFill" x1="0" y1="0" x2="0" y2="1">
        <stop offset="0" stop-color="#9fd0ff" stop-opacity=".6"/>
        <stop offset="1" stop-color="#e6f3ff" stop-opacity=".15"/>
      </linearGradient>
    </defs>
    <g stroke="var(--grid)" stroke-width="1">
      <line x1="372" y1="498" x2="1275" y2="498"/><line x1="372" y1="537" x2="1275" y2="537"/>
      <line x1="372" y1="576" x2="1275" y2="576"/><line x1="372" y1="615" x2="1275" y2="615"/>
      <line x1="372" y1="655" x2="1275" y2="655"/><line x1="372" y1="693" x2="1275" y2="693"/>
    </g>
    <g font-family="Poppins, sans-serif" font-size="8" fill="#6c7684" text-anchor="end">
      <text x="361" y="501">10k</text><text x="361" y="540">08k</text><text x="361" y="579">06k</text>
      <text x="361" y="618">04k</text><text x="361" y="658">02k</text><text x="361" y="702">0</text>
    </g>
    <g font-family="Poppins, sans-serif" font-size="8" fill="#6c7684" text-anchor="middle">
      <text x="392" y="711">01</text><text x="421" y="711">02</text><text x="450" y="711">03</text><text x="479" y="711">04</text>
      <text x="508" y="711">05</text><text x="537" y="711">06</text><text x="566" y="711">07</text><text x="595" y="711">08</text>
      <text x="624" y="711">09</text><text x="653" y="711">10</text><text x="682" y="711">11</text><text x="711" y="711">12</text>
      <text x="740" y="711">13</text><text x="769" y="711">14</text><text x="798" y="711">15</text><text x="827" y="711">16</text>
      <text x="856" y="711">17</text><text x="885" y="711">18</text><text x="914" y="711">19</text><text x="943" y="711">20</text>
      <text x="972" y="711">21</text><text x="1001" y="711">22</text><text x="1030" y="711">23</text><text x="1059" y="711">24</text>
      <text x="1088" y="711">25</text><text x="1117" y="711">26</text><text x="1146" y="711">27</text><text x="1175" y="711">28</text>
      <text x="1204" y="711">29</text><text x="1233" y="711">30</text><text x="1262" y="711">31</text>
    </g>
    <path fill="url(#areaFill)" d="M372,580 C400,560 470,525 530,522 C590,520 640,545 677,577 C720,615 760,650 790,652 C815,655 830,640 845,612 C858,590 870,590 885,592 C915,598 945,625 975,630 C1000,636 1020,620 1040,598 C1070,565 1100,515 1143,498 C1170,485 1195,480 1220,488 C1240,495 1255,510 1266,521 L1266,693 L372,693 Z"/>
    <path fill="none" stroke="#0a8cf0" stroke-width="2.5" d="M372,580 C400,560 470,525 530,522 C590,520 640,545 677,577 C720,615 760,650 790,652 C815,655 830,640 845,612 C858,590 870,590 885,592 C915,598 945,625 975,630 C1000,636 1020,620 1040,598 C1070,565 1100,515 1143,498 C1170,485 1195,480 1220,488 C1240,495 1255,510 1266,521"/>
    <g fill="#0a8cf0" stroke="#fff" stroke-width="1.5">
      <circle cx="391" cy="565" r="4"/><circle cx="437" cy="542" r="4"/><circle cx="555" cy="526" r="4"/>
      <circle cx="677" cy="577" r="5.5"/><circle cx="784" cy="650" r="6"/><circle cx="870" cy="595" r="6"/>
      <circle cx="975" cy="630" r="6.5"/><circle cx="1067" cy="565" r="6.5"/><circle cx="1143" cy="498" r="6.5"/>
      <circle cx="1262" cy="521" r="6"/>
    </g>
  </svg>

  <div class="range"><svg viewBox="0 0 16 16"><rect x="1.5" y="3" width="13" height="11.5"/><path d="M1.5 6.5h13M5 1.5v3M11 1.5v3M4 9h1M7.5 9h1M11 9h1M4 12h1M7.5 12h1M11 12h1"/></svg>12-27-2021 - 01-03-2021</div>

  <div class="filter" style="left:227px">Last 7 days</div>
  <div class="filter" style="left:333px">Last months</div>
  <div class="filter" style="left:439px">Last 3 months</div>
  <div class="filter" style="left:545px">Next 7 days</div>
  <div class="filter" style="left:650px">Next months</div>
  <div class="filter" style="left:755px">Next 3 months</div>

  <div class="legend" style="left:68px;top:315px"><i style="background:#62c4f5"></i>Scheduled Maintenance</div>
  <div class="legend" style="left:241px;top:315px"><i style="background:#8fd66a"></i>Completed Scheduled Maintenance</div>
  <div class="legend" style="left:478px;top:315px"><i style="background:#f59a6b"></i>Future Scheduled Maintenance</div>
  <div class="legend" style="left:689px;top:315px"><i style="background:#f565ac"></i>Scheduled Work Orders</div>
  <div class="legend" style="left:68px;top:332px"><i style="background:#9aa1ab"></i>Completed Work Orders</div>
  <div class="legend" style="left:241px;top:332px"><i style="background:#f7cf5e"></i>Property Inspections in Progress</div>
  <div class="legend" style="left:478px;top:332px"><i style="background:#b07af2"></i>Completed Property Inspections</div>
</section>

<footer class="footer">© Copyrights Domora 2021</footer>

</body>
</html>
```